Company Truck Wrap Design

Truck wrap design. Would like the company logo to look 3d if possible and incorporate blue in the design in with the orange of the logo.

```html
<!DOCTYPE html>
<html lang="en">
<head>
<meta charset="utf-8">
<title>Summit Ridge Roofing – Tailgate Wrap</title>
<link href="https://fonts.googleapis.com/css2?family=Audiowide&family=Orbitron:wght@800;900&family=Ubuntu:wght@500&display=swap" rel="stylesheet">
<style>
  :root {
    --orange-light: #ffa41c;
    --orange: #f68b16;
    --orange-deep: #e9721c;
    --slogan: #d9731f;
    --white: #ffffff;
    --ink: #111111;
    --page: #f4f4f4;
    --badge-dark: #1d1d1d;
    --badge-blue: #2f7fd1;
    --badge-cream: #f3efe6;
  }
  * { margin: 0; padding: 0; box-sizing: border-box; }
  html, body { width: 1200px; height: 929px; overflow: hidden; background: var(--page); }
  .canvas { position: relative; width: 1200px; height: 929px; }

  .window-decal {
    position: absolute; top: 110px; left: 0; width: 1200px;
    text-align: center;
  }
  .brand-name {
    font-family: "Audiowide", sans-serif; font-size: 54px;
    color: var(--orange-deep); letter-spacing: 2px; line-height: 1;
  }
  .brand-tagline {
    margin-top: 8px;
    font-family: "Ubuntu", sans-serif; font-size: 22px; color: var(--ink);
  }

  .tailgate {
    position: absolute; left: 80px; top: 270px; width: 1040px; height: 440px;
    border-radius: 28px; overflow: hidden;
    background: linear-gradient(180deg, var(--orange-light) 0%, var(--orange) 45%, var(--orange-deep) 100%);
  }
  .tailgate::before {
    content: ""; position: absolute; inset: 0;
    background: radial-gradient(ellipse at 0% 0%, rgba(255,214,120,.45), transparent 35%),
                radial-gradient(ellipse at 100% 100%, rgba(255,214,120,.45), transparent 35%);
  }
  .services {
    position: absolute; left: 70px; top: 58px;
    font-family: "Orbitron", sans-serif; font-weight: 900; font-size: 30px;
    color: var(--white); line-height: 1.3; letter-spacing: 1px;
    transform: skewX(-12deg);
  }
  .phone {
    position: absolute; right: 60px; top: 72px;
    font-family: "Audiowide", sans-serif; font-size: 50px;
    color: var(--white); letter-spacing: 3px;
  }
  .message-band {
    position: absolute; left: 0; right: 0; top: 190px; height: 110px;
    background: var(--white); text-align: center; padding-top: 18px;
  }
  .slogan {
    font-family: "Audiowide", sans-serif; font-size: 40px;
    color: var(--slogan); letter-spacing: 3px;
  }
  .website {
    margin-top: 4px;
    font-family: "Ubuntu", sans-serif; font-size: 24px;
    color: var(--ink); letter-spacing: 1.5px;
  }
  .accent-stripe { position: absolute; top: 316px; }
  .accent-stripe.left { left: 0; }
  .accent-stripe.right { right: 0; }
  .badges {
    position: absolute; left: 0; right: 0; top: 330px;
    display: flex; justify-content: center; gap: 14px;
  }
  .badge { width: 52px; height: 52px; border-radius: 50%; border: 3px solid var(--white); }
  .badge.association { background: var(--badge-dark); }
  .badge.inspector { background: var(--badge-blue); }
  .badge.institute { background: var(--badge-cream); }
</style>
</head>
<body>
<div class="canvas">
  <div class="window-decal">
    <div class="brand-name">SUMMIT RIDGE</div>
    <div class="brand-tagline">Roofing and Contracting</div>
  </div>

  <section class="tailgate">
    <div class="services">RESIDENTIAL &amp;<br>COMMERCIAL</div>
    <div class="phone">210-555-0148</div>

    <div class="message-band">
      <div class="slogan">LET’S TALK ABOUT YOUR ROOF!</div>
      <div class="website">www.SummitRidgeRoofsTx.com</div>
    </div>

    <svg class="accent-stripe left" width="300" height="12" viewBox="0 0 300 12" aria-hidden="true">
      <polygon points="0,0 285,0 300,12 0,12" fill="#ffffff"/>
    </svg>
    <svg class="accent-stripe right" width="300" height="12" viewBox="0 0 300 12" aria-hidden="true">
      <polygon points="15,0 300,0 300,12 0,12" fill="#ffffff"/>
    </svg>

    <div class="badges">
      <div class="badge association" role="img" aria-label="Licensed contractor association badge"></div>
      <div class="badge inspector" role="img" aria-label="Certified inspector badge"></div>
      <div class="badge institute" role="img" aria-label="Roofing institute certification badge"></div>
    </div>
  </section>
</div>
</body>
</html>
```